Design a WordPress layout for a home loans company

The home loans company in question is going through a rebrand and needs a new website layout.
Sites they like: http://www.brightkeylending.com.au/
Current logo: Attached.
Colours to be used: As per those used in logo.
Primary: #71aa3d
Secondary: #130e10
Pages to be designed:
- Homepage
- Internal services page
Menu items for display purposes:
- Home
- About Us
- Speak to a Broker
- Articles
- Contact Us
A modern design with simplicity is key.
For copy, dummy text such as Lorem ipsum will be fine.
If you would like anything elso, please ask.
Target Market(s)
25-40 year old
Mostly female
Buying their first home in most cases
Industry/Entity Type
Mortgage Brokerage
Number of Pages Required
2 page

```html
<!DOCTYPE html>
<html lang="en">
<head>
<meta charset="utf-8">
<title>Brightkey Home Loans</title>
<link href="https://fonts.googleapis.com/css2?family=Montserrat:wght@600;700&family=Roboto:wght@400;700&family=Marcellus&family=Open+Sans:wght@400;600&display=swap" rel="stylesheet">
<style>
:root{
  --green:#71aa3d;
  --green-dark:#4f7e25;
  --ink:#130e10;
  --grey-bg:#f1f1f1;
  --panel:#f3f3f3;
  --text:#666;
  --white:#fff;
}
*{margin:0;padding:0;box-sizing:border-box}
html,body{width:1200px;height:2675px;overflow:hidden;background:var(--white)}
body{position:relative;font-family:"Open Sans",sans-serif;color:var(--text)}
.abs{position:absolute}

/* hero */
.hero{left:0;top:0;width:1200px;height:605px;background:linear-gradient(100deg,#e9e6e3 0%,#d9cfc6 35%,#e7dcd5 60%,#f0e8e6 100%)}
.brand{font-family:"Roboto",sans-serif;font-weight:700;color:var(--green);font-size:46px;letter-spacing:-0.5px;text-align:center;width:1200px;left:0}
.hero .brand{top:62px}
.hero-title{left:0;width:1200px;text-align:center;font-family:"Montserrat",sans-serif;font-weight:700;color:var(--ink);line-height:1.05}
.hero-title .small{display:block;font-size:40px;padding-left:30px}
.hero-title .big{display:block;font-size:54px}
.btn-main{left:478px;top:406px;width:242px;height:61px;background:linear-gradient(#5f9630,#2b3d1b);color:var(--white);font-family:"Roboto",sans-serif;font-size:23px;display:flex;align-items:center;justify-content:center}

/* nav */
.nav{left:0;top:605px;width:1200px;height:60px;background:var(--white);border-top:1px solid #e3e3e3}
.nav ul{list-style:none;display:flex;position:absolute;left:201px;top:0;height:60px}
.nav li{font-family:"Marcellus",serif;font-size:16px;color:var(--ink);height:60px;display:flex;align-items:center;padding:0 38px}
.nav li.active{background:var(--ink);color:var(--white);padding:0 27px}
.green-rule{left:0;width:1200px;height:8px;background:var(--green)}
.notch{width:0;height:0;border-left:13px solid transparent;border-right:13px solid transparent;border-top:13px solid var(--green);left:587px}
.shade{left:60px;width:1080px;height:50px;background:radial-gradient(ellipse at top,rgba(0,0,0,.18),rgba(0,0,0,0) 70%)}

/* section titles */
.title{left:0;width:1200px;text-align:center;font-family:"Roboto",sans-serif;font-weight:700;color:var(--ink);font-size:46px}
.title em{font-style:normal;color:var(--green)}

/* about */
.about-bg{left:0;top:674px;width:1200px;height:368px;background:var(--grey-bg)}
.about-lead{left:0;width:1200px;top:816px;text-align:center;font-family:"Marcellus",serif;font-size:20px;color:#333}
.about-copy{left:235px;width:730px;top:855px;text-align:center;font-family:"Marcellus",serif;font-size:14px;line-height:20px;color:#555}
.feature{width:340px;text-align:center}
.feature .disc{margin:0 auto;width:144px;height:144px;border-radius:50%;background:var(--white);box-shadow:0 12px 18px rgba(0,0,0,.08);display:flex;align-items:center;justify-content:center}
.feature h3{font-family:"Roboto",sans-serif;font-size:20px;color:var(--ink);margin-top:48px}
.feature p{font-size:13.5px;line-height:20px;color:#666;margin-top:16px;padding:0 10px}

/* broker */
.broker{left:77px;top:1346px;width:1046px;height:184px;background:var(--panel)}
.broker-photo{left:77px;top:1320px;width:163px;height:210px;background:linear-gradient(#eae4df,#b8aaa2)}
.broker .title{left:0;width:1046px;top:38px;font-size:44px;padding-left:60px}
.field{top:104px;height:41px;background:var(--white);border:1px solid #ddd;font-size:13px;color:#777;padding:12px 14px}
.btn-find{left:784px;top:104px;width:161px;height:41px;background:linear-gradient(#5f9630,#1f2c14);color:var(--white);font-family:"Roboto",sans-serif;font-weight:700;font-size:15px;display:flex;align-items:center;justify-content:center}

/* articles */
.card-panel{top:1692px;width:312px;height:521px;background:var(--panel)}
.card-image{top:1733px;width:449px;height:230px;border:2px solid var(--ink)}
.meta{font-size:13px;color:#888;display:flex;align-items:center;gap:10px}
.card-text{width:270px}
.card-text h4{font-family:"Roboto",sans-serif;font-size:16px;line-height:22px;color:var(--ink)}
.card-text .date{font-size:16px;color:#999;margin-top:10px}
.card-text p{font-size:14px;line-height:22px;color:#666;margin-top:8px}

/* footer */
.footer{left:0;top:2277px;width:1200px;height:398px;background:#0e0e0e}
.footer .brand{top:80px;font-size:44px}
.foot-links{left:0;width:1200px;top:178px;display:flex;justify-content:center;gap:56px;font-family:"Open Sans",sans-serif;font-size:17px;color:#e5e5e5}
.contact{display:flex;align-items:center;gap:22px;color:var(--white);font-size:14px;line-height:21px}
.contact .dot{width:54px;height:54px;border-radius:50%;background:var(--white);display:flex;align-items:center;justify-content:center;flex:none}
.bottom-bar{left:0;top:344px;width:1200px;height:54px;background:linear-gradient(90deg,#111 0%,#4d7e27 45%,#7bb545 60%,#2c4519 85%,#111 100%)}
.social{left:95px;top:20px;display:flex;gap:26px}
.social span{width:12px;height:12px;border-radius:50%;background:var(--white);display:block}
.copyright{right:78px;top:16px;color:var(--white);font-size:14px}
.copyright b{font-family:"Roboto",sans-serif;font-size:17px}
</style>
</head>
<body>

<section class="hero abs" role="img" aria-label="Photo of a broker with a clipboard talking to a smiling family on a sofa">
  <div class="brand abs">Brightkey Home Loans</div>
  <h1 class="hero-title abs" style="top:284px"><span class="small">ARE YOU LOOKING</span><span class="big">FOR HOME LOAN?</span></h1>
  <div class="btn-main abs">FIND OUT MORE</div>
</section>

<nav class="nav abs">
  <ul>
    <li class="active">HOME</li><li>ABOUT US</li><li>SPEAK TO A BROKER</li><li>ARTICLES</li><li>CONTACT US</li>
  </ul>
</nav>

<div class="about-bg abs"></div>
<div class="green-rule abs" style="top:665px"></div>
<div class="notch abs" style="top:673px"></div>
<div class="shade abs" style="top:680px"></div>

<h2 class="title abs" style="top:746px">ABOUT <em>US</em></h2>
<p class="about-lead abs">Lorem Ipsum is simply dummy text of the printing and typesetting industry.</p>
<p class="about-copy abs">Lorem Ipsum is simply dummy text of the printing and typesetting industry. Lorem Ipsum has been the industry's standard dummy text ever since the 1500s, when an unknown printer took a galley of type and scrambled it to make a type specimen book. It has survived not only five centuries, but also the leap into electronic typesetting, remaining essentially unchanged. It was popularised in the 1960s.</p>

<div class="feature abs" style="left:74px;top:969px">
  <div class="disc">
    <svg width="80" height="80" viewBox="0 0 80 80"><rect x="30" y="10" width="30" height="56" fill="none" stroke="#222" stroke-width="2.5"/><g fill="#222"><rect x="36" y="17" width="5" height="5"/><rect x="46" y="17" width="5" height="5"/><rect x="36" y="28" width="5" height="5"/><rect x="46" y="28" width="5" height="5"/><rect x="36" y="39" width="5" height="5"/><rect x="46" y="39" width="5" height="5"/></g><path d="M22 34a12 12 0 0 1 12 12c0 10-12 22-12 22S10 56 10 46a12 12 0 0 1 12-12z" fill="#71aa3d" stroke="#222" stroke-width="2"/><path d="M16 46l4 4 8-8" fill="none" stroke="#fff" stroke-width="3"/></svg>
  </div>
  <h3>Local experts</h3>
  <p>Lorem Ipsum is simply dummy text of the printing and typesetting industry. Lorem Ipsum has been the industry's standard dummy text.</p>
</div>
<div class="feature abs" style="left:429px;top:969px">
  <div class="disc">
    <svg width="80" height="80" viewBox="0 0 80 80"><path d="M8 24h36v22H24l-10 9v-9H8z" fill="#555"/><path d="M34 30h38v24h-6v9l-10-9H34z" fill="#71aa3d"/><rect x="51" y="36" width="4" height="11" fill="#fff"/><rect x="51" y="49" width="4" height="3" fill="#fff"/></svg>
  </div>
  <h3>Ongoing trusted advice</h3>
  <p>Lorem Ipsum is simply dummy text of the printing and typesetting industry. Lorem Ipsum has been the industry's standard dummy text.</p>
</div>
<div class="feature abs" style="left:786px;top:969px">
  <div class="disc">
    <svg width="84" height="84" viewBox="0 0 84 84"><rect x="8" y="38" width="12" height="34" rx="4" fill="#71aa3d"/><path d="M28 40l14-24c6-2 9 2 8 8l-3 12h20c5 0 8 4 7 8l-5 22c-1 4-4 6-8 6H28z" fill="none" stroke="#222" stroke-width="4" stroke-linejoin="round"/></svg>
  </div>
  <h3>Greater choice</h3>
  <p>Lorem Ipsum is simply dummy text of the printing and typesetting industry. Lorem Ipsum has been the industry's standard dummy text.</p>
</div>

<section class="broker abs">
  <h2 class="title abs">SPEAK TO <em>A BROKER</em></h2>
  <div class="field abs" style="left:164px;width:299px">Email</div>
  <div class="field abs" style="left:474px;width:299px">Enter Location Or Postcode</div>
  <div class="btn-find abs">FIND BROKER</div>
</section>
<div class="broker-photo abs" role="img" aria-label="Photo of a smiling broker in a light suit pointing upward"></div>
<div class="green-rule abs" style="top:1528px;left:77px;width:1046px;height:5px"></div>
<div class="notch abs" style="top:1533px"></div>
<div class="shade abs" style="top:1540px"></div>

<h2 class="title abs" style="top:1615px">OUR <em>ARTICLES</em></h2>

<div class="card-panel abs" style="left:253px"></div>
<div class="card-image abs" style="left:77px;background:linear-gradient(#c9b58a,#8a8f5e)" role="img" aria-label="Photo of a couple embracing in front of a new home"></div>
<div class="abs" style="left:93px;top:2018px">
  <div class="meta"><svg width="24" height="20" viewBox="0 0 24 20"><path d="M3 2h18v12H9l-5 4v-4H3z" fill="none" stroke="#71aa3d" stroke-width="2"/></svg>Comments (18)</div>
  <div class="meta" style="margin-top:40px"><svg width="24" height="20" viewBox="0 0 24 20"><path d="M12 18L3 9a5 5 0 0 1 9-5 5 5 0 0 1 9 5z" fill="none" stroke="#71aa3d" stroke-width="2"/></svg>Favorite (16)</div>
  <div class="meta" style="margin-top:40px"><svg width="24" height="20" viewBox="0 0 24 20"><circle cx="6" cy="10" r="3" fill="#71aa3d"/><circle cx="18" cy="4" r="3" fill="#71aa3d"/><circle cx="18" cy="16" r="3" fill="#71aa3d"/><path d="M6 10L18 4M6 10l12 6" stroke="#71aa3d" stroke-width="2"/></svg>Share Post (13)</div>
</div>
<div class="card-text abs" style="left:270px;top:1998px">
  <h4>Lorem Ipsum is simply dummy text of the printing and typesetting.</h4>
  <div class="date">28th May, 2018</div>
  <p>Lorem Ipsum is simply dummy text of the printing and typesetting industry. Lorem Ipsum has been the industry's standard dummy text ever [...]</p>
</div>

<div class="card-panel abs" style="left:811px"></div>
<div class="card-image abs" style="left:635px;background:linear-gradient(#f6d6d0,#e8b9ad)" role="img" aria-label="Photo of a young couple shopping online with a laptop and card"></div>
<div class="abs" style="left:651px;top:2018px">
  <div class="meta"><svg width="24" height="20" viewBox="0 0 24 20"><path d="M3 2h18v12H9l-5 4v-4H3z" fill="none" stroke="#71aa3d" stroke-width="2"/></svg>Comments (18)</div>
  <div class="meta" style="margin-top:40px"><svg width="24" height="20" viewBox="0 0 24 20"><path d="M12 18L3 9a5 5 0 0 1 9-5 5 5 0 0 1 9 5z" fill="none" stroke="#71aa3d" stroke-width="2"/></svg>Favorite (16)</div>
  <div class="meta" style="margin-top:40px"><svg width="24" height="20" viewBox="0 0 24 20"><circle cx="6" cy="10" r="3" fill="#71aa3d"/><circle cx="18" cy="4" r="3" fill="#71aa3d"/><circle cx="18" cy="16" r="3" fill="#71aa3d"/><path d="M6 10L18 4M6 10l12 6" stroke="#71aa3d" stroke-width="2"/></svg>Share Post (13)</div>
</div>
<div class="card-text abs" style="left:830px;top:1998px">
  <h4>Lorem Ipsum is simply dummy text of the printing and typesetting.</h4>
  <div class="date">28th May, 2018</div>
  <p>Lorem Ipsum is simply dummy text of the printing and typesetting industry. Lorem Ipsum has been the industry's standard dummy text ever [...]</p>
</div>

<footer class="footer abs">
  <div class="brand abs">Brightkey Home Loans</div>
  <nav class="foot-links abs"><span>About</span><span>Service</span><span>Beauty Products</span><span>Testimonial</span><span>Contact</span></nav>
  <div class="contact abs" style="left:75px;top:236px">
    <span class="dot"><svg width="20" height="24" viewBox="0 0 20 24"><path d="M10 1a8 8 0 0 1 8 8c0 6-8 14-8 14S2 15 2 9a8 8 0 0 1 8-8z" fill="#111"/><circle cx="10" cy="9" r="3" fill="#fff"/></svg></span>
    <span>Lorem ipsum dolor sit amet,<br>consectetur adipiscing elit,<br>Country 123456.</span>
  </div>
  <div class="contact abs" style="left:524px;top:240px">
    <span class="dot"><svg width="22" height="22" viewBox="0 0 24 24"><path d="M6 2l4 5-2 3c1 3 3 5 6 6l3-2 5 4-3 4C10 22 2 14 2 5z" fill="#111"/></svg></span>
    <span>123 456 7878</span>
  </div>
  <div class="contact abs" style="left:882px;top:240px">
    <span class="dot"><svg width="22" height="18" viewBox="0 0 22 18"><rect x="1" y="2" width="20" height="14" fill="#111"/><path d="M1 3l10 7 10-7" fill="none" stroke="#fff" stroke-width="1.5"/></svg></span>
    <span>sales@brightkeyloans.com</span>
  </div>
  <div class="bottom-bar abs">
    <div class="social abs"><span></span><span></span><span></span><span></span></div>
    <div class="copyright abs">© <b>Brightkey Home Loans</b> - 2018. All Rights Reserved.</div>
  </div>
</footer>

</body>
</html>
```